WordPress website design for wealth management company

A modern clean look website for a service company. This is mostly for information only, with a form to capture prospect contact information and schedule a 15 minutes call. There will be several static pages describe what services we offer, how we are different, and a blog section for posting articles and share resources. A section for client testimonials.
I want a website that is easy to understand and maintain. No proprietary plugins that cost extra. The main thing I need help is the visual layout / color palette that present a clean and professional look, select the suitable stock photos that convey the image of trust, professional, innovative, and high service.
Some websites with style I like include the following
- https://www.halvorbrook.com/
- https://www.trivanplanningworks.com/
- https://morvellfunds.com/private-equity-partners/
Also some websites in other industries with clean modern look
- https://zentrell.com/
- https://quovra.com/
- https://www.plumtorvik.com/
I want the end product to be a fully functional website that I can upload into web hosting service I use and I can easily add content and maintain myself in the future.

```html
<!DOCTYPE html>
<html lang="en">
<head>
<meta charset="utf-8">
<title>Brightmoor Wealth</title>
<link href="https://fonts.googleapis.com/css2?family=Montserrat:wght@400;500;600;700;800&display=swap" rel="stylesheet">
<style>
:root{
  --purple:#5b2d8e;
  --purple-deep:#4d2479;
  --yellow:#fbbd2a;
  --footer-bar:#e4d12b;
  --ink:#161616;
  --text:#3a3a3a;
  --grey-bg:#f4f4f4;
  --card-bg:#efefef;
  --white:#ffffff;
}
*{box-sizing:border-box;margin:0;padding:0}
html,body{width:1200px;height:4191px;overflow:hidden}
body{font-family:'Montserrat',sans-serif;color:var(--text);background:var(--white);position:relative}
.abs{position:absolute}

/* Header */
.header{position:absolute;left:0;top:0;width:1200px;height:107px;background:var(--white)}
.brand{position:absolute;left:90px;top:40px;width:160px;text-align:center}
.brand-name{font-weight:600;font-size:19px;letter-spacing:2px;color:var(--purple);line-height:1}
.topbar-item{position:absolute;top:8px;display:flex;align-items:center;gap:16px;font-size:15px;color:var(--ink)}
.icon-badge{width:38px;height:38px;border-radius:50%;background:var(--yellow);display:flex;align-items:center;justify-content:center}
.nav{position:absolute;left:244px;top:62px;width:956px;height:45px;background:var(--yellow);clip-path:polygon(28px 0,100% 0,100% 100%,0 100%)}
.nav a{position:absolute;top:13px;font-size:15px;font-weight:500;color:var(--ink);text-decoration:none}

/* Hero */
.hero{position:absolute;left:0;top:107px;width:1200px;height:517px;background:linear-gradient(100deg,#eef5fb 0%,#dbeaf5 45%,#8fc0d9 75%,#4b8fb0 100%)}
.hero h1{position:absolute;left:98px;top:98px;font-size:56px;line-height:66px;font-weight:500;color:var(--ink)}
.hero h1 strong{font-weight:700}
.hero h1 .accent{color:var(--purple)}
.hero p{position:absolute;left:98px;top:249px;width:430px;font-size:13px;line-height:23px;color:var(--ink)}
.btn-pill{position:absolute;display:flex;align-items:center;justify-content:center;background:var(--yellow);border:2px solid var(--purple);border-radius:22px;font-weight:500;color:var(--ink)}

/* Different */
.mark-block{position:absolute;left:81px;top:711px;width:447px;height:411px;display:flex;align-items:center;justify-content:center}
.mark-block span{font-size:50px;font-weight:600;color:var(--purple);letter-spacing:2px}
.section-title{font-weight:700;color:var(--ink);text-transform:uppercase}
.diff-title{position:absolute;left:598px;top:720px;font-size:38px;line-height:51px}
.diff-text{position:absolute;left:600px;top:835px;width:485px;font-size:14.5px;line-height:31.5px;color:var(--text)}

/* Services */
.services{position:absolute;left:0;top:1223px;width:1200px;height:595px;background:var(--grey-bg)}
.center-title{position:absolute;left:0;width:1200px;text-align:center;font-size:38px}
.service-card{position:absolute;top:162px;width:240px;height:371px;border-radius:3px;overflow:hidden}
.service-card .label{position:absolute;left:20px;bottom:38px;width:200px;font-size:19px;line-height:27px;font-weight:700;color:var(--white)}

/* Testimonials */
.testimonial{position:absolute;left:177px;top:2028px;width:846px;height:245px;background:var(--card-bg);border-radius:4px;text-align:center}
.testimonial h3{margin-top:44px;font-size:21px;font-weight:600;color:var(--ink)}
.testimonial p{width:760px;margin:30px auto 0;font-size:15px;line-height:25px;color:var(--text)}
.avatar{position:absolute;top:2239px;width:75px;height:75px;border-radius:50%;border:3px solid var(--purple);background:linear-gradient(160deg,#e9e4dd,#b9a898)}
.avatar.active{top:2233px;width:86px;height:86px}

/* Blog */
.post{position:absolute;top:2514px;width:320px}
.post-photo{width:320px;height:229px;position:relative}
.date{position:absolute;left:16px;top:14px;width:46px;height:72px;background:var(--white);border-radius:3px;font-size:25px;font-weight:700;line-height:30px;color:var(--ink);text-align:center;padding-top:6px}
.post h3{margin-top:22px;text-align:center;font-size:27px;font-weight:600;color:var(--ink)}
.post p{margin:14px auto 0;width:300px;text-align:center;font-size:15px;line-height:30px;color:var(--text)}

/* Schedule */
.schedule{position:absolute;left:0;top:2968px;width:1200px;height:687px;background:linear-gradient(180deg,var(--purple) 0%,var(--purple-deep) 100%)}
.schedule .center-title{color:var(--white);top:110px}
.field{position:absolute;background:var(--white);border-radius:8px;border:1px solid #ddd;font-size:14px;color:var(--ink);padding:16px 16px}
.send{position:absolute;left:504px;top:549px;width:213px;height:65px;background:var(--yellow);border-radius:33px;display:flex;align-items:center;justify-content:center;gap:20px;font-size:22px;font-weight:600;color:var(--ink)}

/* Footer */
.footer-brand{position:absolute;left:0;top:3840px;width:1200px;text-align:center}
.footer-brand .brand-name{font-size:38px;letter-spacing:5px}
.contact{position:absolute;top:3966px;display:flex;gap:17px}
.contact .dot{width:36px;height:36px;border-radius:50%;background:var(--ink);display:flex;align-items:center;justify-content:center;flex:none}
.contact h4{font-size:16px;font-weight:600;color:var(--ink);letter-spacing:.5px}
.contact p{font-size:14px;line-height:22px;color:var(--ink)}
.footer-nav{position:absolute;left:0;top:4046px;width:1200px;height:66px;background:var(--footer-bar)}
.footer-nav a{position:absolute;top:22px;font-size:17px;color:var(--ink);text-decoration:none}
.copyright{position:absolute;left:0;top:4136px;width:1200px;text-align:center;font-size:17px;color:var(--ink)}
</style>
</head>
<body>

<header class="header">
  <div class="brand">
    <div class="brand-name">BRIGHTMOOR</div>
  </div>
  <div class="topbar-item" style="left:340px">
    <span class="icon-badge"><svg width="16" height="16" viewBox="0 0 16 16"><circle cx="6.5" cy="6.5" r="4.5" fill="none" stroke="#161616" stroke-width="2"/><line x1="10" y1="10" x2="14" y2="14" stroke="#161616" stroke-width="2.4" stroke-linecap="round"/></svg></span>Search
  </div>
  <div class="topbar-item" style="left:522px">
    <span class="icon-badge"><svg width="16" height="16" viewBox="0 0 24 24"><path fill="#161616" d="M6.6 10.8a15 15 0 0 0 6.6 6.6l2.2-2.2c.3-.3.7-.4 1-.2 1.1.4 2.3.6 3.6.6.6 0 1 .4 1 1V20c0 .6-.4 1-1 1C10.6 21 3 13.4 3 4c0-.6.4-1 1-1h3.5c.6 0 1 .4 1 1 0 1.2.2 2.4.6 3.6.1.3 0 .7-.2 1z"/></svg></span>+1 555-014-2290
  </div>
  <div class="topbar-item" style="left:768px">
    <span class="icon-badge"><svg width="16" height="14" viewBox="0 0 16 12"><rect x="0" y="0" width="16" height="12" rx="1.5" fill="#161616"/><path d="M1 1l7 6 7-6" fill="none" stroke="#fbbd2a" stroke-width="1.5"/></svg></span>info@brightmoorwealth.com
  </div>
  <nav class="nav">
    <a style="left:59px">Home</a>
    <a style="left:162px">About Us</a>
    <a style="left:288px">Services We Offer</a>
    <a style="left:477px">Client Testimonials</a>
    <a style="left:678px">Blog</a>
    <a style="left:768px">Contact Us</a>
  </nav>
</header>

<section class="hero">
  <div class="abs" role="img" aria-label="Photo of a hand touching a tablet with rising financial charts and health icons" style="left:0;top:0;width:1200px;height:517px"></div>
  <h1>Welcome to<br><strong>Brightmoor <span class="accent">Wealth</span></strong></h1>
  <p>Sed ut perspiciatis unde omnis iste natus error sit voluptatem accusantium doloremque laudantium, totam rem aperiam, eaque ipsa quae ab illo</p>
  <div class="btn-pill" style="left:100px;top:340px;width:144px;height:38px;font-size:13px">Get Started</div>
</section>

<section>
  <div class="mark-block"><span>BRIGHTMOOR</span></div>
  <h2 class="section-title diff-title">How we<br>are different</h2>
  <p class="diff-text">Sed ut perspiciatis unde omnis iste natus error sit voluptatem accusantium doloremque laudantium, totam rem aperiam, eaque ipsa quae ab illo inventore veritatis et quasi architecto beatae vitae dicta sunt explicabo. Nemo enim ipsam voluptatem quia voluptas sit aspernatur aut odit aut fugit, sed quia consequuntur magni dolores eos qui ratione voluptatem sequi nesciunt. Neque porro quisquam est, qui dolorem ipsum</p>
  <div class="btn-pill" style="left:602px;top:1076px;width:144px;height:42px;font-size:14px">Read More</div>
</section>

<section class="services">
  <h2 class="section-title center-title" style="top:66px">Services We Offer</h2>
  <div class="service-card" style="left:98px" role="img" aria-label="Photo of a doctor and colleague working at a laptop"><div style="position:absolute;inset:0;background:linear-gradient(180deg,#d9cfc4 0%,#8a7b6e 60%,#3a332e 100%)"></div><div class="label">Sed ut perspiciatis unde</div></div>
  <div class="service-card" style="left:359px" role="img" aria-label="Photo of a smiling professional in a white coat"><div style="position:absolute;inset:0;background:linear-gradient(180deg,#e9e7e3 0%,#9a8f86 60%,#3b3430 100%)"></div><div class="label">Sed ut perspiciatis unde</div></div>
  <div class="service-card" style="left:611px" role="img" aria-label="Photo of hands holding a glowing health shield"><div style="position:absolute;inset:0;background:linear-gradient(180deg,#0e2436 0%,#1c5670 55%,#0a1a28 100%)"></div><div class="label">Sed ut perspiciatis unde</div></div>
  <div class="service-card" style="left:860px" role="img" aria-label="Photo of a business advisor with a nurse reviewing a clipboard"><div style="position:absolute;inset:0;background:linear-gradient(180deg,#e6e8ea 0%,#7d8590 60%,#22262c 100%)"></div><div class="label">Sed ut perspiciatis unde</div></div>
</section>

<section>
  <h2 class="section-title center-title" style="top:1910px">Client Testimonials</h2>
  <svg class="abs" style="left:143px;top:2139px" width="20" height="26" viewBox="0 0 20 26"><path d="M15 3L5 13l10 10" fill="none" stroke="#5b2d8e" stroke-width="4"/></svg>
  <svg class="abs" style="left:1045px;top:2139px" width="20" height="26" viewBox="0 0 20 26"><path d="M5 3l10 10L5 23" fill="none" stroke="#5b2d8e" stroke-width="4"/></svg>
  <div class="testimonial">
    <h3>Nemo enim ipsam</h3>
    <p>Lorem ipsum dolor sit amet, consectetur adipiscing elit, sed do eiusmod tempor incididunt ut labore et dolore magna aliqua. Ut enim ad minim veniam, quis nostrud exercitation ullamco laboris nisi ut aliquip ex ea commodo consequat.</p>
  </div>
  <div class="avatar" style="left:455px" role="img" aria-label="Client portrait photo"></div>
  <div class="avatar active" style="left:557px" role="img" aria-label="Client portrait photo"></div>
  <div class="avatar" style="left:665px" role="img" aria-label="Client portrait photo"></div>
</section>

<section>
  <h2 class="section-title center-title" style="top:2435px">Our Blog</h2>
  <article class="post" style="left:98px">
    <div class="post-photo" role="img" aria-label="Photo of a hand with floating digital health icons" style="background:linear-gradient(135deg,#1a2c4a,#3f6c9c 60%,#1b2438)"><div class="date">09<br>23</div></div>
    <h3>Ut enim ad minima</h3>
    <p>Lorem ipsum dolor sit amet, consectetur adipiscing elit, sed do eiusmod tempor incididunt ut</p>
  </article>
  <article class="post" style="left:439px">
    <div class="post-photo" role="img" aria-label="Photo of a doctor greeting a senior client" style="background:linear-gradient(135deg,#f0efec,#cfc6bb 60%,#a49382)"><div class="date">09<br>23</div></div>
    <h3>Ut enim ad minima</h3>
    <p>Lorem ipsum dolor sit amet, consectetur adipiscing elit, sed do eiusmod tempor incididunt ut</p>
  </article>
  <article class="post" style="left:779px">
    <div class="post-photo" role="img" aria-label="Photo of a doctor and advisor reviewing a tablet" style="background:linear-gradient(135deg,#dfe3e6,#7b8a98 60%,#2e3540)"><div class="date">09<br>23</div></div>
    <h3>Ut enim ad minima</h3>
    <p>Lorem ipsum dolor sit amet, consectetur adipiscing elit, sed do eiusmod tempor incididunt ut</p>
  </article>
</section>

<section class="schedule">
  <h2 class="section-title center-title">Schedule a 15 minutes call</h2>
  <div class="field" style="left:206px;top:213px;width:397px;height:47px">First Name</div>
  <div class="field" style="left:618px;top:213px;width:398px;height:47px">Last Name</div>
  <div class="field" style="left:206px;top:276px;width:397px;height:46px">Phone number</div>
  <div class="field" style="left:618px;top:276px;width:398px;height:46px">Email Address</div>
  <div class="field" style="left:208px;top:349px;width:805px;height:118px">Message</div>
  <div class="send">Send Now <svg width="14" height="12" viewBox="0 0 14 12"><path d="M1 1l5 5-5 5M7 1l5 5-5 5" fill="none" stroke="#161616" stroke-width="2"/></svg></div>
</section>

<footer>
  <div class="footer-brand">
    <div class="brand-name">BRIGHTMOOR</div>
  </div>
  <div class="contact" style="left:114px">
    <span class="dot"><svg width="16" height="12" viewBox="0 0 16 12"><rect width="16" height="12" rx="1.5" fill="#fff"/><path d="M1 1l7 6 7-6" fill="none" stroke="#161616" stroke-width="1.5"/></svg></span>
    <div><h4>EMAIL</h4><p>info@brightmoor.com</p></div>
  </div>
  <div class="contact" style="left:444px">
    <span class="dot"><svg width="14" height="18" viewBox="0 0 14 18"><path d="M7 0a7 7 0 0 0-7 7c0 5 7 11 7 11s7-6 7-11a7 7 0 0 0-7-7z" fill="#fff"/><circle cx="7" cy="7" r="2.5" fill="#161616"/></svg></span>
    <div><h4>OUR LOCATION</h4><p>19 Nemo enim Ipsam voluptatem<br>quia voluptas sit</p></div>
  </div>
  <div class="contact" style="left:804px">
    <span class="dot"><svg width="16" height="16" viewBox="0 0 24 24"><path fill="#fff" d="M6.6 10.8a15 15 0 0 0 6.6 6.6l2.2-2.2c.3-.3.7-.4 1-.2 1.1.4 2.3.6 3.6.6.6 0 1 .4 1 1V20c0 .6-.4 1-1 1C10.6 21 3 13.4 3 4c0-.6.4-1 1-1h3.5c.6 0 1 .4 1 1 0 1.2.2 2.4.6 3.6.1.3 0 .7-.2 1z"/></svg></span>
    <div><h4>PHONE NUMBER</h4><p>+1 555-014-2290</p></div>
  </div>
  <nav class="footer-nav">
    <a style="left:159px">Home</a>
    <a style="left:274px">About Us</a>
    <a style="left:414px">Services We Offer</a>
    <a style="left:623px">Client Testimonials</a>
    <a style="left:847px">Blog</a>
    <a style="left:947px">Contact Us</a>
  </nav>
  <p class="copyright">Copyright © 2023 Brightmoor - All Rights Reserved.</p>
</footer>

</body>
</html>
```